Business Card Design needed for start up company Halvora

In need of a new business card designed for a start up company based in Sydney, Halvora is a new start up innovative Company, our mission it to make property accessible for everyday Australian and to become the leading Real Estate platform in Australia. We want it to be fresh and clean.

Industry/Entity Type

Financial

Contact Information for Business Card

Section for Name
Section for Title

HALVORA - The Strength of Pooling
Mobile:
Direct:

Font styles to use
Sans Serif

Colors
33a6d7
0692cd
0255a3
ffffff

Requirements
Must have
• Logo, all business card details

```html
<!DOCTYPE html>
<html lang="en">
<head>
<meta charset="utf-8">
<title>Halvora Business Card</title>
<link rel="stylesheet" href="https://fonts.googleapis.com/css2?family=Montserrat:wght@600;700;800&family=Open+Sans:wght@400;600&display=swap">
<style>
  :root {
    --sky: #33a6d7;
    --azure: #0692cd;
    --navy: #0255a3;
    --light-sky: #4cbaea;
    --white: #ffffff;
    --charcoal: #2f2f31;
    --ink: #333333;
    --title: #5a6fc6;
    --backdrop: #e6e8eb;
  }
  html, body {
    margin: 0;
    padding: 0;
    width: 1200px;
    height: 1000px;
    overflow: hidden;
    background: var(--backdrop);
  }
  .canvas {
    position: relative;
    width: 1200px;
    height: 1000px;
  }
  .card {
    position: absolute;
    left: 220px;
    width: 760px;
    height: 420px;
    box-shadow: 0 12px 30px rgba(0,0,0,0.22);
    overflow: hidden;
  }
  /* Front */
  .card-front {
    top: 50px;
    background: linear-gradient(35deg, var(--navy) 0%, #2f7cc6 45%, var(--light-sky) 100%);
  }
  .brand {
    position: absolute;
    display: flex;
    align-items: center;
    gap: 14px;
    color: var(--white);
    font-family: "Montserrat", sans-serif;
    font-weight: 800;
    white-space: nowrap;
  }
  .brand-dot {
    border-radius: 50%;
    background: var(--white);
    flex: none;
  }
  .card-front .brand {
    left: 50%;
    top: 180px;
    transform: translateX(-50%);
    font-size: 58px;
    letter-spacing: -1px;
  }
  .card-front .brand-dot { width: 58px; height: 58px; }
  .tagline {
    position: absolute;
    right: 60px;
    bottom: 40px;
    margin: 0;
    color: var(--white);
    font-family: "Open Sans", sans-serif;
    font-size: 14px;
    letter-spacing: 3px;
  }
  /* Back */
  .card-back {
    top: 520px;
    background: var(--white);
  }
  .side-panel {
    position: absolute;
    left: 0; top: 0;
    width: 320px;
    height: 420px;
  }
  .card-back .brand {
    left: 136px;
    top: 210px;
    transform: translate(-50%, -50%) rotate(-90deg);
    font-size: 60px;
    letter-spacing: -1px;
  }
  .card-back .brand-dot { width: 60px; height: 60px; }
  .details {
    position: absolute;
    left: 330px;
    top: 58px;
    font-family: "Open Sans", sans-serif;
    color: var(--ink);
  }
  .person-name {
    margin: 0;
    font-family: "Montserrat", sans-serif;
    font-weight: 700;
    font-size: 30px;
    color: var(--sky);
    line-height: 1.1;
  }
  .person-title {
    margin: 0;
    font-family: "Montserrat", sans-serif;
    font-weight: 700;
    font-size: 19px;
    color: var(--title);
  }
  .address {
    margin: 48px 0 0;
    font-size: 18px;
    line-height: 1.25;
  }
  .address svg { display: block; margin-bottom: 6px; }
  .contacts {
    list-style: none;
    margin: 40px 0 0;
    padding: 0;
    font-size: 20px;
    line-height: 1.3;
  }
  .contacts li {
    display: flex;
    align-items: center;
    gap: 16px;
  }
  .contacts svg { width: 14px; height: 14px; flex: none; }
  .contact-text { white-space: nowrap; }
  .web-accent { color: var(--sky); }
</style>
</head>
<body>
<main class="canvas">

  <section class="card card-front" aria-label="Card front">
    <div class="brand"><span class="brand-dot"></span><span>HALVORA</span></div>
    <p class="tagline">The Strength of Pooling</p>
  </section>

  <section class="card card-back" aria-label="Card back">
    <svg class="side-panel" viewBox="0 0 320 420" role="img" aria-label="Dark side panel with faint world map texture">
      <path d="M0 0 H300 V110 C300 150 250 140 250 180 V420 H0 Z" fill="var(--charcoal)"/>
      <path d="M262 175 C262 165 268 158 276 154 V420 H262 Z" fill="var(--sky)"/>
    </svg>
    <div class="brand"><span class="brand-dot"></span><span>HALVORA</span></div>

    <div class="details">
      <h1 class="person-name">Daniel Reyes</h1>
      <p class="person-title">Director</p>

      <p class="address">
        <svg width="16" height="16" viewBox="0 0 16 16" aria-hidden="true"><path d="M1 7 L15 1 L9 15 L7 9 Z" fill="none" stroke="var(--sky)" stroke-width="1.3"/></svg>
        Your Street Address,<br>Australia, 1234
      </p>

      <ul class="contacts">
        <li><svg viewBox="0 0 14 14" aria-hidden="true"><path d="M3 1 L5 1 L6 4 L4.5 5 C5.5 7 7 8.5 9 9.5 L10 8 L13 9 L13 11 C13 12 12 13 11 13 C6 13 1 8 1 3 C1 2 2 1 3 1 Z" fill="var(--sky)"/></svg><span class="contact-text">000 123 444 555</span></li>
        <li><svg viewBox="0 0 14 14" aria-hidden="true"><rect x="3.5" y="0.5" width="7" height="13" rx="1.2" fill="none" stroke="var(--sky)"/><circle cx="7" cy="11.3" r="0.8" fill="var(--sky)"/></svg><span class="contact-text">000 444 5555</span></li>
        <li><svg viewBox="0 0 14 14" aria-hidden="true"><rect x="0.5" y="2.5" width="13" height="9" fill="var(--sky)"/><path d="M0.5 2.5 L7 8 L13.5 2.5" fill="none" stroke="var(--white)"/></svg><span class="contact-text">danielr@email.com</span></li>
        <li><svg viewBox="0 0 14 14" aria-hidden="true"><circle cx="8" cy="6" r="4.5" fill="none" stroke="var(--sky)" stroke-width="1.4"/><path d="M4.8 9.2 L1 13" stroke="var(--sky)" stroke-width="1.6"/></svg><span class="contact-text">www.<span class="web-accent">yourdomain</span>.com</span></li>
      </ul>
    </div>
  </section>

</main>
</body>
</html>
```